KestrelCourse

Take the information and positional images that I have supplied (in the inDesign doc) and design a contemporary clean corporate brochure better than supplied. I would like an indesign or layered photoshop file back so that I can place the highres images in when I have finished and also the contact details when I get a number (not supplied) yet. I would like to use prussian blue and match it to other material that I am having made.

I'd like the design to be strong and dynamic as it is the first print run and will need sever other design concepts to compliment it. When one great and unique design comes through I am start with other brochures that fit in with it.

Its tailored to HR managers, but its an arts based training program so an element of visual sophistication would be advantageous.
Updates

Hi ........It will be printed on a matt eco/recycled card (which will absorb a lot of ink and be somewhat flat)

Dear Designers I am uploading some high res images to use in the layout which will be A5 6 page foldout. Thanks, have a great day!

Hi Designers, the design should be more than, and potentially different to what I supplied. It can be similar but I am actually looking for a more sophisticated design than what I suppled. Thank you.

Hi Designers, thanks so much for your designs so far. My feeling is that I may have confused the brief, I would prefer if the design was not the same as mine, the reason I have submitted my design to ArtMarketHub is so that I could have a different design. This brochure will go out to 3000 people so I want it to look strong and sophisticated. I am also going to create 4-5 other designs from this one to go in packs, so this design (its my first time with ArtMarketHub) needs to be strong so that everything else can be moulded against it. I haven't submitted the other briefs yet as it would be a waste of time until the first one is done. Thank you kindly.

Target Market(s)

Corporates & HR Managers

Industry/Entity Type

Training

Requirements
Must have
• Logo and prussian blue as a colour. An inDesign (CS5) file returned so I can drop hi res positionals in at a later stage.
Should not have
• Flattened files as details for this brochure are not finalised

```html
<!DOCTYPE html>
<html lang="en">
<head>
<meta charset="utf-8">
<title>KestrelCourse brochure – Lumivance</title>
<link rel="stylesheet" href="https://fonts.googleapis.com/css2?family=Jost:wght@300;400;500;600&family=Crimson+Pro:ital,wght@1,400&display=swap">
<style>
  :root {
    --prussian: #2e4d8f;
    --prussian-dark: #233c72;
    --ink: #3a3a3a;
    --grey: #6b6b6b;
    --paper: #ffffff;
    --stage: #111111;
    --pattern-light: #dfe3ec;
  }
  * { box-sizing: border-box; margin: 0; padding: 0; }
  html, body { width: 1200px; height: 900px; overflow: hidden; background: var(--stage); }
  body { font-family: "Jost", sans-serif; color: var(--ink); }

  .brochure { position: absolute; left: 60px; top: 195px; width: 1080px; height: 510px; display: flex; }
  .panel { position: relative; width: 360px; height: 510px; background: var(--paper); overflow: hidden; }
  .panel--middle { background: linear-gradient(90deg, #ececec 0%, #ffffff 12%, #ffffff 100%); }

  .heading { font-size: 20px; line-height: 1; letter-spacing: 0.3px; text-transform: uppercase; }
  .heading .light { font-weight: 300; }
  .heading .bold { font-weight: 600; }

  /* Panel 1 */
  .how-box { position: absolute; left: 22px; top: 20px; width: 300px; height: 150px; background: var(--prussian); color: #fff; border-radius: 10px 10px 10px 0; padding: 12px 10px; }
  .how-box .heading { color: #fff; margin-bottom: 5px; }
  .how-box p { font-size: 7.3px; line-height: 1.45; }
  .how-box .choose { display: flex; margin-top: 8px; font-size: 7.3px; line-height: 1.45; }
  .how-box .choose span:first-child { width: 56px; }
  .meetups { position: absolute; left: 28px; top: 180px; width: 310px; }
  .meetups .title-row { display: flex; align-items: flex-end; border-left: 3px solid var(--prussian); padding-left: 5px; }
  .meetups .heading { color: var(--prussian); font-size: 21px; }
  .meetups .rule { flex: 1; height: 2px; background: var(--prussian); margin: 0 0 4px 6px; }
  .meetups .lead { font-size: 10px; line-height: 1.3; margin-top: 3px; }
  .meetups h3 { font-size: 9px; font-weight: 600; margin-top: 10px; text-transform: uppercase; }
  .meetups .cols { display: flex; gap: 12px; margin-top: 3px; }
  .meetups .cols p { flex: 1; font-size: 6.8px; line-height: 1.45; }
  .photo { position: absolute; top: 355px; height: 155px; }
  .photo--stage { left: 0; width: 152px; background: linear-gradient(160deg, #4a3a30, #1b1410); }
  .photo--speaker { left: 157px; width: 203px; background: linear-gradient(200deg, #3a3430, #0e0c0b); }

  /* Panel 2 */
  .deco-corner { position: absolute; left: 0; top: 18px; width: 62px; height: 40px; background: linear-gradient(135deg, var(--prussian), #8a9cc4); opacity: 0.85; }
  .intro { position: absolute; left: 28px; top: 55px; width: 318px; font-size: 7.3px; line-height: 1.45; color: var(--grey); }
  .intro .brand { font-size: 22px; font-weight: 400; color: var(--prussian); margin-right: 4px; line-height: 1; }
  .intro p + p { margin-top: 9px; }
  .tutor { position: absolute; left: 28px; top: 160px; width: 318px; }
  .tutor .title-row { display: flex; align-items: flex-end; border-left: 3px solid var(--prussian); padding-left: 5px; }
  .tutor .heading { color: var(--prussian); font-size: 21px; }
  .tutor .rule { flex: 1; height: 2px; background: var(--prussian); margin: 0 0 4px 6px; }
  .tutor .bio { font-size: 7.3px; line-height: 1.45; color: var(--grey); margin-top: 3px; }
  .tutor .bio strong { font-weight: 600; color: var(--ink); }
  .testimonials { position: absolute; left: 28px; top: 220px; width: 318px; display: flex; gap: 10px; }
  .feature-quote { width: 148px; border-left: 3px solid var(--prussian); padding-left: 6px; }
  .feature-quote blockquote { font-family: "Crimson Pro", serif; font-style: italic; font-size: 15.5px; line-height: 1.22; color: var(--grey); }
  .quote-mark { font-family: "Crimson Pro", serif; font-style: italic; color: var(--prussian); font-size: 26px; line-height: 0; vertical-align: -7px; }
  .cite { font-size: 6.2px; line-height: 1.4; color: var(--ink); margin-top: 6px; }
  .cite b { font-weight: 500; text-transform: uppercase; display: block; }
  .side-quotes { flex: 1; padding-top: 2px; }
  .side-quotes blockquote { font-family: "Crimson Pro", serif; font-style: italic; font-size: 8.4px; line-height: 1.3; color: var(--grey); }
  .side-quotes figure + figure { margin-top: 16px; }
  .side-quotes .cite { margin-top: 2px; }
  .contact-bar { position: absolute; left: 20px; top: 484px; width: 330px; height: 20px; background: linear-gradient(90deg, #7d95c4, var(--prussian)); border-radius: 0 8px 8px 0; color: #fff; font-size: 6.5px; display: flex; align-items: center; gap: 8px; padding-left: 14px; }

  /* Panel 3 */
  .pattern-field { position: absolute; left: 0; top: 0; width: 360px; height: 290px; background: radial-gradient(ellipse at 50% 40%, #6a82b8 0%, var(--prussian) 45%, var(--pattern-light) 100%); opacity: 0.9; }
  .closing-quote { position: absolute; left: 40px; top: 310px; width: 280px; text-align: center; font-family: "Crimson Pro", serif; font-style: italic; font-size: 16.5px; line-height: 1.3; color: var(--grey); }
  .closing-quote .attrib { display: block; font-family: "Jost", sans-serif; font-style: normal; font-size: 7px; letter-spacing: 0.5px; margin-top: 4px; }
  .brand-box { position: absolute; left: 52px; top: 420px; width: 245px; height: 90px; background: var(--prussian); border-radius: 10px 10px 0 0; color: #fff; display: flex; flex-direction: column; align-items: center; justify-content: center; gap: 6px; }
  .brand-box .row { display: flex; align-items: center; gap: 8px; }
  .brand-box .mark { width: 14px; height: 14px; border: 2px solid #fff; }
  .brand-box .name { font-size: 24px; font-weight: 300; line-height: 1; }
  .brand-box .tagline { font-size: 7.5px; font-weight: 300; }
</style>
</head>
<body>
<main class="brochure">

  <section class="panel panel--left">
    <div class="how-box">
      <h2 class="heading"><span class="light">How it </span><span class="bold">Works</span></h2>
      <p>The <strong>KESTREL</strong>COURSE runs from your boardroom minimising collective travel time. We work with a group of 5 people per session (you can hold multiple sessions over different days). There are 12 hours of group/tuition time that can be factored in to suit your business environment accomodating how long you can engage your team in training.</p>
      <div class="choose"><span>Choose from:</span><span>2 hours over 6 weeks; or<br>3 hours over 4 weeks; or<br>6 hours over 2 weeks</span></div>
    </div>
    <div class="meetups">
      <div class="title-row"><h2 class="heading"><span class="bold">Meet</span><span class="light"> ups</span></h2><span class="rule"></span></div>
      <p class="lead">Meetups are an engaging way to satisify your teams need for socialisation. Meetups run for one hour and can allow participation of up to 100 people.</p>
      <h3>Lunchtime &amp; Afternoon Lectures</h3>
      <div class="cols">
        <p>We will come to your boardroom and spend time together involving your staff in a visually rich, culturally engaging discussion of the many of histories of art and photography with particular reference to Australian content, ignighting debate, and facilitating participation and life enriching skills.</p>
        <p>The lectures run for one hour and organisations are encouraged to allow time for group social participation after the talks to allow staff to engage with each other, reflecting on the talk, expressing their own opinions, listening to others while learning great good stuff in the process.</p>
      </div>
    </div>
    <div class="photo photo--stage" role="img" aria-label="Photo of a speaker presenting on a lit stage to a seated audience"></div>
    <div class="photo photo--speaker" role="img" aria-label="Photo of the tutor speaking at a lectern beside a laptop"></div>
  </section>

  <section class="panel panel--middle">
    <div class="deco-corner" role="img" aria-label="Small cluster of nested square outlines"></div>
    <div class="intro">
      <p><span class="brand">Lumivance</span> is a unique concept whereby we will come to your premises and teach your staff the fundamentals of photography with emphasis on personal and interpersonal development within a group environment.</p>
      <p>The learning programs we run are both artistic and holistic in nature. The study of art and photography within the work place builds self confidence and enhances motivation and enthusiasm especially given photography is an integral part of all of our lives. Students learn together and have the opportunity to develop individual forms of self expression in their own time, increasing self awareness. As they rejoin and express their individuality, healthier relationships and bonding with colleagues develop.</p>
    </div>
    <div class="tutor">
      <div class="title-row"><h2 class="heading"><span class="light">Your </span><span class="bold">Tutor</span></h2><span class="rule"></span></div>
      <p class="bio"><strong>MARLA QUINNELL</strong> holds a Masters Degree in Visual Art, majoring in PhotoMedia from Harbourside Arts College, Eastvale University. Marla has been lecturing &amp; mentoring for over a decade in art, photography, creative and personal development.</p>
    </div>
    <div class="testimonials">
      <figure class="feature-quote">
        <blockquote><span class="quote-mark">&ldquo;</span> Marla has a great knowledge of her subject and is very enthusiastic in her teaching methodology. She is able to produce high quality results from both beginning students as well as from more mature students.&rdquo;</blockquote>
        <figcaption class="cite"><b>— Daniel Korvath</b>Chair of PhotoMedia<br>Harbourside Arts College,<br>Eastvale University (May 2011)</figcaption>
      </figure>
      <div class="side-quotes">
        <figure>
          <blockquote>&ldquo;On a personal level, I have found Marla an absolute joy to work with and she was become a mentor for me.&rdquo;</blockquote>
          <figcaption class="cite"><b>— Owen Tresidder</b>Associate Director<br>Creative Learning<br>The Southern Lens Institute</figcaption>
        </figure>
        <figure>
          <blockquote>&ldquo;I noticed a marked difference in the compatibility of my team almost immediately.&rdquo;</blockquote>
          <figcaption class="cite"><b>— Rita Hallam</b>Director, Cobaltine</figcaption>
        </figure>
        <figure>
          <blockquote>&ldquo;Very clever and outstanding technique for motivating staff and encouraging teambuilding.&rdquo;</blockquote>
          <figcaption class="cite"><b>— Grant Ellery</b>Norvane Systems</figcaption>
        </figure>
      </div>
    </div>
    <footer class="contact-bar"><span>12 Wattle Lane Ashby NSW 2040</span><span>|</span><span>www.lumivance.me</span><span>|</span><span>hello@lumivance.me</span><span>|</span><span>0400 000 123</span></footer>
  </section>

  <section class="panel panel--cover">
    <div class="pattern-field" role="img" aria-label="Scattered pattern of nested blue square outlines"></div>
    <p class="closing-quote"><span class="quote-mark">&ldquo;</span> The strength of the team is each individual member. The strength of each member is the team. <span class="quote-mark">&rdquo;</span><span class="attrib">— DALE RANSOM</span></p>
    <div class="brand-box">
      <div class="row"><span class="mark"></span><span class="name">lumivance.me</span></div>
      <span class="tagline">Mentoring a lifestyle of art photography and digital media</span>
    </div>
  </section>

</main>
</body>
</html>
```